Real Estate Webpage Design

We have an existing website: ferndaleestatecollective.com.au
We focus customised service mainly on Property Management and second-hand property sales.
We are not entirely happy about the current design and layout can stay roughly the same as the back end coding is linked to a CRM system.
We would like to see the design are more reachable to our clients and appearing.
Please check our Website Design Draft for more details.

Industry/Entity Type

Real estate Agency

Number of Pages Required

5+ page

Font styles to use
Sans Serif

Colors

Designer to choose colors to be used in the design.

```html
<!DOCTYPE html>
<html lang="en">
<head>
<meta charset="utf-8">
<title>Ferndale Estate Collective – For Lease</title>
<link href="https://fonts.googleapis.com/css2?family=Poppins:wght@400;500;600&display=swap" rel="stylesheet">
<style>
:root{
  --gold:#ecbd55;
  --navy:#1f3a5f;
  --navy-dark:#172d4b;
  --footer:#13233d;
  --footer-line:#24364f;
  --ink:#1b2433;
  --muted:#6b7280;
  --line:#d9dde3;
}
*{box-sizing:border-box;margin:0;padding:0}
html,body{width:1200px;height:2208px;overflow:hidden}
body{font-family:'Poppins',sans-serif;color:var(--ink);background:#fff;position:relative}
.abs{position:absolute}
svg.ic{display:block}

/* hero */
.hero{left:0;top:0;width:1200px;height:411px;background:linear-gradient(100deg,#f7f8f9 0%,#eef0f2 35%,#d9dde0 60%,#c9ced2 80%,#b9bfc4 100%)}
.logo{left:60px;top:16px;display:flex;align-items:center;gap:10px}
.logo-mark{width:44px;height:44px;border:4px solid var(--gold)}
.logo-name{font-size:26px;font-weight:600;color:var(--navy);line-height:1}
.logo-sub{font-size:11px;letter-spacing:1.5px;color:var(--navy);margin-top:4px}
.nav{left:435px;top:27px;display:flex;gap:0;font-size:14px;color:#2a3446}
.nav a{text-decoration:none;color:inherit;margin-right:26px}
.btn-add{left:1013px;top:19px;width:126px;height:35px;background:var(--gold);color:#fff;font-size:14px;display:flex;align-items:center;justify-content:center}
.hero-title{left:62px;top:156px;font-size:38px;font-weight:600;color:var(--navy)}
.hero-title span{color:var(--gold)}
.hero-sub{left:62px;top:210px;font-size:14px;color:#1b2433}
.btn-see{left:60px;top:253px;width:150px;height:35px;background:var(--gold);color:#fff;font-size:14px;display:flex;align-items:center;justify-content:center}

/* search */
.search{left:60px;top:393px;width:1080px;height:68px;background:#fff;box-shadow:0 3px 8px rgba(0,0,0,.12);display:flex;align-items:center}
.search-type{width:114px;height:100%;border-right:1px solid var(--line);display:flex;align-items:center;justify-content:space-between;padding:0 14px 0 17px;font-size:14px}
.search-input{flex:1;padding-left:13px;font-size:14px;color:#8a8f98}
.search-btn{width:45px;height:45px;background:var(--gold);margin-right:12px;display:flex;align-items:center;justify-content:center}

/* filters */
.filters{left:60px;top:551px;width:1080px;height:54px;border:1px solid #5a6372;display:flex}
.filters div{flex:1;border-right:1px solid #5a6372;display:flex;align-items:center;justify-content:space-between;padding:0 14px 0 18px;font-size:14px}
.filters div:last-child{border-right:none}

/* cards */
.card{width:517px;height:428px;background:#fff;box-shadow:0 2px 8px rgba(0,0,0,.08)}
.card-head{height:45px;background:var(--navy);display:flex;align-items:center;color:#fff;position:relative}
.card-pin{width:58px;height:100%;background:var(--navy-dark);display:flex;align-items:center;justify-content:center}
.card-loc{padding-left:9px;line-height:1.25}
.card-loc b{font-size:14px;font-weight:600;display:block}
.card-loc small{font-size:12.5px}
.card-star{position:absolute;right:28px;top:10px}
.card-img{height:208px;position:relative}
.card-price{position:absolute;left:14px;bottom:22px;color:#fff;font-size:16px;font-weight:600;text-shadow:0 1px 3px rgba(0,0,0,.4)}
.card-next{position:absolute;right:22px;bottom:28px;width:26px;height:26px;background:var(--navy);display:flex;align-items:center;justify-content:center}
.card-feat{display:flex;align-items:center;gap:8px;padding:26px 0 0 23px;font-size:14px}
.card-feat svg{margin-left:14px}
.card-feat svg:first-child{margin-left:0}
.card-insp{padding:15px 0 0 23px;font-size:18px;font-weight:500}
.card-date{padding:4px 0 0 23px;font-size:14px;color:var(--gold);font-weight:500}
.card-foot{position:absolute;left:0;bottom:0;width:100%;height:42px;border-top:1px solid #c7ccd3;display:flex;align-items:center;padding:0 20px}
.avatar{width:31px;height:31px;background:linear-gradient(#a9b0b9,#7f8792)}
.agent{margin-left:11px;font-size:14px;flex:1}
.foot-icons{display:flex;gap:8px}

/* cta */
.cta{left:0;top:1635px;width:1200px;height:226px;background:var(--gold);text-align:center}
.cta h2{margin-top:50px;font-size:23px;line-height:34px;font-weight:600;color:#fff}
.cta-btn{display:inline-block;margin-top:23px;background:var(--navy);color:#fff;font-size:14px;padding:8px 16px;border:1px solid #fff}

/* footer */
.footer{left:0;top:1861px;width:1200px;height:309px;background:var(--footer);color:#fff}
.f-logo{left:60px;top:48px;display:flex;align-items:center;gap:12px}
.f-logo .logo-mark{border-color:#fff;width:50px;height:50px}
.f-logo .logo-name,.f-logo .logo-sub{color:#fff}
.f-about{left:61px;top:125px;font-size:13px;line-height:22px;width:210px}
.f-h{font-size:14px;font-weight:600;color:var(--gold)}
.sitemap{left:329px;top:50px}
.sitemap ul{list-style:none;margin-top:16px}
.sitemap li{font-size:13px;height:27px;display:flex;align-items:center;gap:6px}
.contact{left:613px;top:50px}
.c-row{display:flex;gap:10px;font-size:13px;line-height:20px;margin-top:14px}
.social{left:889px;top:50px}
.social-row{display:flex;gap:16px;margin-top:22px}
.social-row span{width:39px;height:39px;border-radius:50%;border:2px solid var(--gold);display:flex;align-items:center;justify-content:center;font-size:12px;font-weight:600}
.social-row span:first-child{background:var(--gold);color:var(--footer)}
.bottom{left:0;top:2170px;width:1200px;height:38px;background:var(--footer);border-top:1px solid var(--footer-line);color:#fff;font-size:12.5px;display:flex;align-items:center;padding:0 61px}
.bottom .links{margin-left:auto;display:flex;gap:22px}
</style>
</head>
<body>

<svg width="0" height="0" style="position:absolute">
  <defs>
    <symbol id="i-pin" viewBox="0 0 24 24"><path d="M12 21s-7-7-7-12a7 7 0 0 1 14 0c0 5-7 12-7 12z" fill="none" stroke="currentColor" stroke-width="1.5"/><circle cx="12" cy="9" r="2.6" fill="none" stroke="currentColor" stroke-width="1.5"/></symbol>
    <symbol id="i-star" viewBox="0 0 24 24"><path d="M12 2l3 6.6 7.2.8-5.4 4.9 1.5 7.1L12 17.8 5.7 21.4l1.5-7.1L1.8 9.4 9 8.6z" fill="currentColor"/></symbol>
    <symbol id="i-bed" viewBox="0 0 26 20"><path d="M2 18V4h22v14M2 12h22M5 12V8h7v4M14 12V8h7v4" fill="none" stroke="currentColor" stroke-width="1.4"/></symbol>
    <symbol id="i-bath" viewBox="0 0 26 20"><path d="M3 10h20v3a5 5 0 0 1-5 5H8a5 5 0 0 1-5-5zM7 10V3h4" fill="none" stroke="currentColor" stroke-width="1.4"/></symbol>
    <symbol id="i-car" viewBox="0 0 28 18"><path d="M2 12l2-5 5-3h9l5 4 3 1v4H2zM6 14a2 2 0 1 0 4 0M18 14a2 2 0 1 0 4 0" fill="none" stroke="currentColor" stroke-width="1.4"/></symbol>
    <symbol id="i-clock" viewBox="0 0 24 24"><circle cx="12" cy="12" r="9" fill="none" stroke="currentColor" stroke-width="1.6"/><path d="M12 7v5l3 2" fill="none" stroke="currentColor" stroke-width="1.6"/></symbol>
    <symbol id="i-expand" viewBox="0 0 24 24"><path d="M4 9V4h5M15 4h5v5M20 15v5h-5M9 20H4v-5M4 4l6 6M20 4l-6 6M20 20l-6-6M4 20l6-6" fill="none" stroke="currentColor" stroke-width="1.6"/></symbol>
    <symbol id="i-mail" viewBox="0 0 24 24"><rect x="2.5" y="5" width="19" height="14" fill="none" stroke="currentColor" stroke-width="1.6"/><path d="M3 6l9 7 9-7M3 18l6-6M21 18l-6-6" fill="none" stroke="currentColor" stroke-width="1.6"/></symbol>
    <symbol id="i-phone" viewBox="0 0 24 24"><path d="M6 3l3 1 1 5-2 1.5a11 11 0 0 0 5.5 5.5L15 14l5 1 1 3-2 3C11 21 3 13 3 5z" fill="none" stroke="currentColor" stroke-width="1.4"/></symbol>
    <symbol id="i-caret" viewBox="0 0 12 8"><path d="M0 0h12L6 7z" fill="currentColor"/></symbol>
    <symbol id="i-chev" viewBox="0 0 12 12"><path d="M4 1l5 5-5 5" fill="none" stroke="currentColor" stroke-width="1.5"/></symbol>
    <symbol id="i-arrow" viewBox="0 0 20 8"><path d="M0 4h18M14 1l4 3-4 3" fill="none" stroke="currentColor" stroke-width="1"/></symbol>
  </defs>
</svg>

<section class="hero abs" role="img" aria-label="Bright white living and dining room interior with sofas, dining table and mirror"></section>

<div class="logo abs">
  <div class="logo-mark"></div>
  <div><div class="logo-name">Ferndale Estate</div><div class="logo-sub">Collective</div></div>
</div>
<nav class="nav abs"><a>Home</a><a>About Us</a><a>Leasing</a><a>Buy</a><a>Sell</a><a>Our Team</a><a>Blog</a><a>Contact Us</a></nav>
<div class="btn-add abs">Add Properties</div>

<h1 class="hero-title abs">For <span>Lease</span></h1>
<p class="hero-sub abs">Your local real estate property group</p>
<div class="btn-see abs">See All Properties</div>

<div class="search abs">
  <div class="search-type">Rent <svg class="ic" width="13" height="8" style="color:#1b2433"><use href="#i-caret"/></svg></div>
  <div class="search-input">Search by Suburb, Postcode or keyword</div>
  <div class="search-btn"><svg width="24" height="24" viewBox="0 0 24 24"><circle cx="10" cy="10" r="7" fill="none" stroke="#fff" stroke-width="2"/><path d="M15 15l6 6" stroke="#fff" stroke-width="2"/></svg></div>
</div>

<div class="filters abs">
  <div>category <svg width="10" height="7"><use href="#i-caret"/></svg></div>
  <div>Price min <svg width="10" height="7"><use href="#i-caret"/></svg></div>
  <div>Price max <svg width="10" height="7"><use href="#i-caret"/></svg></div>
  <div>Beds <svg width="10" height="7"><use href="#i-caret"/></svg></div>
  <div>Baths <svg width="10" height="7"><use href="#i-caret"/></svg></div>
  <div>Parking <svg width="10" height="7"><use href="#i-caret"/></svg></div>
</div>

<!-- listing cards -->
<article class="card abs" style="left:60px;top:657px">
  <div class="card-head"><div class="card-pin"><svg width="24" height="26" style="color:#fff"><use href="#i-pin"/></svg></div><div class="card-loc"><b>Kellerwood</b><small>Level 3/42/7 Wattle Crest Avenue...</small></div><svg class="card-star" width="24" height="24" style="color:var(--gold)"><use href="#i-star"/></svg></div>
  <div class="card-img" role="img" aria-label="Single-storey brick house with garage under a cloudy blue sky" style="background:linear-gradient(180deg,#8fb5e0 0%,#c9d8e8 35%,#9a7a66 55%,#b8b3ab 80%,#8aa06a 100%)"><span class="card-price">$369,900+</span><span class="card-next"><svg width="12" height="12" style="color:#fff"><use href="#i-chev"/></svg></span></div>
  <div class="card-feat"><svg width="22" height="17" style="color:var(--gold)"><use href="#i-bed"/></svg>2<svg width="22" height="17" style="color:var(--gold)"><use href="#i-bath"/></svg>2<svg width="26" height="17" style="color:var(--gold)"><use href="#i-car"/></svg>1</div>
  <div class="card-insp">Next Inspection:</div>
  <div class="card-date">Sat 21st May 9:40 Am-10:00 Am</div>
  <div class="card-foot"><div class="avatar"></div><div class="agent">Mia Harlow</div><div class="foot-icons"><svg width="18" height="18"><use href="#i-clock"/></svg><svg width="18" height="18"><use href="#i-expand"/></svg><svg width="20" height="18"><use href="#i-mail"/></svg></div></div>
</article>

<article class="card abs" style="left:622px;top:657px">
  <div class="card-head"><div class="card-pin"><svg width="24" height="26" style="color:#fff"><use href="#i-pin"/></svg></div><div class="card-loc"><b>Kellerwood</b><small>Level 3/42/7 Wattle Crest Avenue...</small></div><svg class="card-star" width="24" height="24" style="color:var(--gold)"><use href="#i-star"/></svg></div>
  <div class="card-img" role="img" aria-label="Rooftop infinity pool beside an apartment tower overlooking bushland" style="background:linear-gradient(180deg,#b8c6d2 0%,#9eaab2 35%,#4a6fb0 60%,#2f55a0 100%)"><span class="card-price">$369,900+</span><span class="card-next"><svg width="12" height="12" style="color:#fff"><use href="#i-chev"/></svg></span></div>
  <div class="card-feat"><svg width="22" height="17" style="color:var(--gold)"><use href="#i-bed"/></svg>2<svg width="22" height="17" style="color:var(--gold)"><use href="#i-bath"/></svg>2<svg width="26" height="17" style="color:var(--gold)"><use href="#i-car"/></svg>1</div>
  <div class="card-insp">Next Inspection:</div>
  <div class="card-date">Sat 21st May 9:40 Am-10:00 Am</div>
  <div class="card-foot"><div class="avatar"></div><div class="agent">Mia Harlow</div><div class="foot-icons"><svg width="18" height="18"><use href="#i-clock"/></svg><svg width="18" height="18"><use href="#i-expand"/></svg><svg width="20" height="18"><use href="#i-mail"/></svg></div></div>
</article>

<article class="card abs" style="left:60px;top:1122px">
  <div class="card-head"><div class="card-pin"><svg width="24" height="26" style="color:#fff"><use href="#i-pin"/></svg></div><div class="card-loc"><b>Kellerwood</b><small>Level 3/42/7 Wattle Crest Avenue...</small></div><svg class="card-star" width="24" height="24" style="color:var(--gold)"><use href="#i-star"/></svg></div>
  <div class="card-img" role="img" aria-label="Living room with patterned sofa, rug and timber floor" style="background:linear-gradient(160deg,#6d6258 0%,#a39a90 40%,#8a5a32 75%,#6e4325 100%)"><span class="card-price">$369,900+</span><span class="card-next"><svg width="12" height="12" style="color:#fff"><use href="#i-chev"/></svg></span></div>
  <div class="card-feat"><svg width="22" height="17" style="color:var(--gold)"><use href="#i-bed"/></svg>2<svg width="22" height="17" style="color:var(--gold)"><use href="#i-bath"/></svg>2<svg width="26" height="17" style="color:var(--gold)"><use href="#i-car"/></svg>1</div>
  <div class="card-insp">Next Inspection:</div>
  <div class="card-date">Sat 21st May 9:40 Am-10:00 Am</div>
  <div class="card-foot"><div class="avatar"></div><div class="agent">Mia Harlow</div><div class="foot-icons"><svg width="18" height="18"><use href="#i-clock"/></svg><svg width="18" height="18"><use href="#i-expand"/></svg><svg width="20" height="18"><use href="#i-mail"/></svg></div></div>
</article>

<article class="card abs" style="left:622px;top:1122px">
  <div class="card-head"><div class="card-pin"><svg width="24" height="26" style="color:#fff"><use href="#i-pin"/></svg></div><div class="card-loc"><b>Kellerwood</b><small>Level 3/42/7 Wattle Crest Avenue...</small></div><svg class="card-star" width="24" height="24" style="color:var(--gold)"><use href="#i-star"/></svg></div>
  <div class="card-img" role="img" aria-label="Kitchen with light timber cabinets, oven and dark benchtop" style="background:linear-gradient(180deg,#d8d2c8 0%,#cbbfa8 45%,#b9a888 70%,#4b4b4e 100%)"><span class="card-price">$369,900+</span><span class="card-next"><svg width="12" height="12" style="color:#fff"><use href="#i-chev"/></svg></span></div>
  <div class="card-feat"><svg width="22" height="17" style="color:var(--gold)"><use href="#i-bed"/></svg>2<svg width="22" height="17" style="color:var(--gold)"><use href="#i-bath"/></svg>2<svg width="26" height="17" style="color:var(--gold)"><use href="#i-car"/></svg>1</div>
  <div class="card-insp">Next Inspection:</div>
  <div class="card-date">Sat 21st May 9:40 Am-10:00 Am</div>
  <div class="card-foot"><div class="avatar"></div><div class="agent">Mia Harlow</div><div class="foot-icons"><svg width="18" height="18"><use href="#i-clock"/></svg><svg width="18" height="18"><use href="#i-expand"/></svg><svg width="20" height="18"><use href="#i-mail"/></svg></div></div>
</article>

<section class="cta abs">
  <h2>Contact Us If You Want To Sell Your House Or You<br>Have Other Questions</h2>
  <span class="cta-btn">Request Free Consultation</span>
</section>

<footer class="footer abs">
  <div class="f-logo abs"><div class="logo-mark"></div><div><div class="logo-name">Ferndale Estate</div><div class="logo-sub">Collective</div></div></div>
  <p class="f-about abs">Lorem ipsum dolor sit amet, consectetur adipiscing elit, sed do eiusmod tempor...</p>

  <div class="sitemap abs">
    <div class="f-h">Site Map</div>
    <ul>
      <li><svg width="20" height="8"><use href="#i-arrow"/></svg>Home</li>
      <li><svg width="20" height="8"><use href="#i-arrow"/></svg>About Us</li>
      <li><svg width="20" height="8"><use href="#i-arrow"/></svg>Leasing</li>
      <li><svg width="20" height="8"><use href="#i-arrow"/></svg>Buy</li>
      <li><svg width="20" height="8"><use href="#i-arrow"/></svg>Sell</li>
      <li><svg width="20" height="8"><use href="#i-arrow"/></svg>Our Team</li>
      <li><svg width="20" height="8"><use href="#i-arrow"/></svg>Blog</li>
      <li><svg width="20" height="8"><use href="#i-arrow"/></svg>Contact Us</li>
    </ul>
  </div>

  <div class="contact abs">
    <div class="f-h">Contact Us</div>
    <div class="c-row" style="margin-top:22px"><svg width="22" height="22"><use href="#i-pin"/></svg><span>218/4 Wattle Crest Rd, Kellerwood<br>, ACT, 2900</span></div>
    <div class="c-row"><svg width="22" height="22"><use href="#i-phone"/></svg><b style="font-weight:600;line-height:23px">02 6000 3127<br>02 6000 5894</b></div>
    <div class="c-row"><svg width="22" height="22"><use href="#i-mail"/></svg><span>info@ferndaleestate.com.au</span></div>
  </div>

  <div class="social abs">
    <div class="f-h">Follow On Us</div>
    <div class="social-row"><span>IG</span><span>FB</span><span>YT</span><span>TW</span></div>
  </div>
</footer>

<div class="bottom abs">
  <span>2022© Ferndale Estate Collective. All right reserved.</span>
  <div class="links"><span>Privacy</span><span>Complaint Handling &amp; Dispute Resolution</span><span>Due Diligence Checklist</span></div>
</div>

</body>
</html>
```